Compelling Senior Home Care highlight live-in home care and couples care

Compelling High end client who is looking to advertise and highlight their live-in home care and couples care. Their name is Meadowlark Home Health Services and their website is https://www.meadowlarkhhs-example.com/ Please use their current website colors and I attached some examples.

Specs:

Non-Medical Care or
Home Health Grid Ad
3.85w x 3h

Ad should have:
LOGO
WEBSITE
PHONE NUMBER
(BUTTON - Find Out More)
Text Variations:
We Give People the Help They Need to Live in the Place They Love (see example for exact look and feel)
Do you or your loved one need care at home?
Live at home as long as possible!
Caregivers You Can Trust
Caregivers That Come On Time
Caregivers That Live with You
High Level Care
Hours Match Your Needs

PVG is produced in Macintosh platform CS6. Please create your ads in these programs. Please submit
your ads in high-resolution camera-ready PDF, TIF or EPS format: 300 DPI at 100% of printed size, all
colors CMYK, all fonts and graphics embedded. Use POSTSCRIPT TYPE 1 fonts when possible, TRUE TYPE
FONTS may not print correctly. If submitting native files, please include all linked graphics and fonts.
NOTE: if your ad is not produced by the PVG Art Staff, a professional Ad Agency or Design firm, and is
not properly constructed for technical electronic digital printing, the final printed product may not print
correctly and may differ from your screen proof. Please flightcheck your ad before submitting to PVG.
Publisher reserves the right to charge for all costs incurred in preparation of material submitted that
does not meet the Elders Pine Guide digital specifications.
• All colors, logos, and images in your ad need to be CMYK builds at 300 dpi at 100% size
• Construct your file document size to our size specifications and save your PDF to 100% of size

Target Market(s)

Adults taking care of mom and dad

Industry/Entity Type

Home Health Care

Requirements
Nice to have
• PLEASE SEE EXAMPLES
Should not have
• BORING

```html
<!DOCTYPE html>
<html lang="en">
<head>
<meta charset="utf-8">
<title>Meadowlark Home Health Services – Grid Ad</title>
<link rel="stylesheet" href="https://fonts.googleapis.com/css2?family=Dancing+Script:wght@700&family=Montserrat:wght@600;800&family=Mulish:wght@400;500;700;800&display=swap">
<style>
  :root {
    --plum: #8a2465;
    --plum-deep: #6e1a50;
    --blush: #f8e6f0;
    --heart-faint: #e9c3d8;
    --ink: #2a2a2a;
    --white: #ffffff;
    --stage: #2b2b2b;
  }
  * { margin: 0; padding: 0; box-sizing: border-box; }
  html, body { width: 1200px; height: 1177px; overflow: hidden; background: var(--stage); }
  .ad {
    position: absolute; left: 74px; top: 199px;
    width: 1042px; height: 811px;
    background: var(--white); overflow: hidden;
    font-family: "Mulish", sans-serif; color: var(--ink);
  }
  .ad-shapes { position: absolute; inset: 0; }
  .brand {
    position: absolute; left: 60px; top: 170px;
    display: flex; align-items: center; gap: 16px;
  }
  .brand-mark { width: 44px; height: 44px; background: var(--plum); }
  .brand-name {
    font-family: "Mulish", sans-serif; font-weight: 800;
    font-size: 30px; line-height: 1.1; color: var(--plum); width: 380px;
  }
  .headline {
    position: absolute; left: 34px; top: 284px;
    font-size: 43px; font-weight: 500; line-height: 1.27; color: var(--ink);
  }
  .headline strong { color: var(--plum); font-weight: 800; }
  .tagline {
    position: absolute; left: 34px; top: 414px; width: 520px;
    border-top: 2px solid var(--plum); border-bottom: 2px solid var(--plum);
    padding: 6px 0 10px 2px;
    font-family: "Dancing Script", cursive; font-weight: 700;
    font-size: 40px; line-height: 1.2; color: var(--plum);
  }
  .features {
    position: absolute; left: 34px; top: 498px; list-style: none;
    font-size: 24px; line-height: 37.6px; color: var(--ink);
  }
  .features li { position: relative; padding-left: 30px; }
  .features li svg { position: absolute; left: 0; top: 10px; width: 20px; height: 18px; }
  .promise {
    position: absolute; right: 30px; top: 640px; text-align: right;
  }
  .promise-title {
    font-family: "Montserrat", sans-serif; font-weight: 800;
    font-size: 35px; line-height: 1.1; color: var(--plum); letter-spacing: 0.2px;
  }
  .promise-sub { font-size: 23px; line-height: 1.4; color: var(--ink); font-weight: 500; }
  .contact-bar {
    position: absolute; left: 0; bottom: 0; width: 100%; height: 84px;
    background: var(--plum); display: flex; align-items: center;
    padding-left: 24px; color: var(--white);
    font-family: "Montserrat", sans-serif; font-weight: 600;
    white-space: nowrap;
  }
  .contact-item { display: flex; align-items: center; gap: 12px; margin-right: 22px; }
  .contact-icon {
    width: 40px; height: 40px; border-radius: 50%; background: var(--white);
    display: flex; align-items: center; justify-content: center; flex-shrink: 0;
  }
  .contact-phone { font-size: 23px; }
  .contact-web { font-size: 17px; letter-spacing: 0; }
  .cta-button {
    position: absolute; right: 30px; top: 19px;
    width: 262px; height: 48px; border-radius: 24px; background: var(--white);
    display: flex; align-items: center; justify-content: center; gap: 14px;
    font-family: "Montserrat", sans-serif; font-weight: 800; font-size: 21px; color: var(--ink);
    text-decoration: none;
  }
</style>
</head>
<body>
<div class="ad">
  <svg class="ad-shapes" width="1042" height="811" viewBox="0 0 1042 811">
    <defs>
      <linearGradient id="caregiverPhotoTone" x1="0" y1="0" x2="1" y2="1">
        <stop offset="0" stop-color="#d9c9bd"/>
        <stop offset="0.5" stop-color="#b9a68f"/>
        <stop offset="1" stop-color="#d8d2c8"/>
      </linearGradient>
      <linearGradient id="outdoorPhotoTone" x1="0" y1="0" x2="1" y2="1">
        <stop offset="0" stop-color="#7f9a6a"/>
        <stop offset="0.6" stop-color="#a9b6c4"/>
        <stop offset="1" stop-color="#8b5a78"/>
      </linearGradient>
    </defs>
    <path class="blush-field" d="M330 727 C460 640 720 575 1042 545 V727 Z" fill="var(--blush)"/>
    <path class="plum-sweep" d="M0 0 H1042 V472 C920 462 800 445 700 425 C600 300 520 95 300 72 C170 60 60 108 0 150 Z" fill="var(--plum)"/>
    <path d="M520 0 H1042 V430 C930 424 820 410 730 396 C640 270 600 120 520 0 Z" fill="url(#caregiverPhotoTone)" role="img" aria-label="Photo: a caregiver in a plum uniform laughing with an elderly woman seated in a chair"/>
    <path class="faint-heart" d="M965 590 C945 574 935 564 935 552 C935 542 943 536 951 536 C957 536 962 540 965 545 C968 540 973 536 979 536 C987 536 995 542 995 552 C995 564 985 574 965 590 Z" fill="var(--heart-faint)"/>
    <circle cx="808" cy="497" r="128" fill="var(--plum)"/>
    <circle cx="808" cy="497" r="113" fill="var(--white)"/>
    <circle cx="808" cy="497" r="105" fill="url(#outdoorPhotoTone)" role="img" aria-label="Photo: a caregiver hugging a smiling older man in a wheelchair outdoors"/>
  </svg>

  <div class="brand">
    <span class="brand-mark"></span>
    <span class="brand-name">Meadowlark Home Health Services</span>
  </div>

  <h1 class="headline">Do you or your loved one<br>need <strong>CARE</strong> at home?</h1>

  <p class="tagline">Live at home as long as possible!</p>

  <ul class="features">
    <li><svg viewBox="0 0 20 18"><path d="M10 18 C4 13 0 10 0 5 C0 2 2 0 5 0 C7 0 9 1 10 3 C11 1 13 0 15 0 C18 0 20 2 20 5 C20 10 16 13 10 18 Z" fill="var(--plum)"/></svg>Hourly, live-in, 24/7 and Couples Care Options</li>
    <li><svg viewBox="0 0 20 18"><path d="M10 18 C4 13 0 10 0 5 C0 2 2 0 5 0 C7 0 9 1 10 3 C11 1 13 0 15 0 C18 0 20 2 20 5 C20 10 16 13 10 18 Z" fill="var(--plum)"/></svg>Assistance with activities of daily living &amp; safety</li>
    <li><svg viewBox="0 0 20 18"><path d="M10 18 C4 13 0 10 0 5 C0 2 2 0 5 0 C7 0 9 1 10 3 C11 1 13 0 15 0 C18 0 20 2 20 5 C20 10 16 13 10 18 Z" fill="var(--plum)"/></svg>High Quality Caregivers with<br>Dementia &amp; Parkinson's expertise</li>
    <li><svg viewBox="0 0 20 18"><path d="M10 18 C4 13 0 10 0 5 C0 2 2 0 5 0 C7 0 9 1 10 3 C11 1 13 0 15 0 C18 0 20 2 20 5 C20 10 16 13 10 18 Z" fill="var(--plum)"/></svg>Serving all of Massachusetts</li>
  </ul>

  <div class="promise">
    <p class="promise-title">WE GIVE PEOPLE THE HELP</p>
    <p class="promise-sub">They Need to live in the Place They Love</p>
  </div>

  <div class="contact-bar">
    <div class="contact-item">
      <span class="contact-icon">
        <svg width="22" height="22" viewBox="0 0 24 24"><path d="M6.6 10.8c1.4 2.8 3.8 5.1 6.6 6.6l2.2-2.2c.3-.3.7-.4 1-.2 1.1.4 2.3.6 3.6.6.6 0 1 .4 1 1V20c0 .6-.4 1-1 1C10.6 21 3 13.4 3 4c0-.6.4-1 1-1h3.5c.6 0 1 .4 1 1 0 1.3.2 2.5.6 3.6.1.3 0 .7-.2 1L6.6 10.8z" fill="var(--plum)"/></svg>
      </span>
      <span class="contact-phone">555-014-3711</span>
    </div>
    <div class="contact-item">
      <span class="contact-icon">
        <svg width="24" height="24" viewBox="0 0 24 24" fill="none" stroke="var(--plum)" stroke-width="2"><circle cx="12" cy="12" r="9"/><ellipse cx="12" cy="12" rx="4" ry="9"/><line x1="3" y1="12" x2="21" y2="12"/></svg>
      </span>
      <span class="contact-web">WWW.MEADOWLARKHHS-EXAMPLE.COM</span>
    </div>
    <a class="cta-button" href="https://www.meadowlarkhhs-example.com/">FIND OUT MORE
      <svg width="28" height="28" viewBox="0 0 28 28"><circle cx="14" cy="14" r="14" fill="var(--plum)"/><path d="M11 8 L19 14 L11 20 Z" fill="var(--white)"/></svg>
    </a>
  </div>
</div>
</body>
</html>
```